Flyer for an anniversary promotion

2nd year anniversary promotion flyer for Copperleaf Dental (logo attached)
Size A4
Promotion runs from Now until 31st Dec 2024
Leave room for actual promotional text which will be in multiple languages (~50 words)
Brand associations
Modern, classy, high quality service, customer care

NOTE - Company SELLS to dental clinics but Copperleaf is a dental products company, not dentists/dental clinics/etc.

Plumvistar wants this to be 300+ words

Target Market(s)

Dental clinics

Industry/Entity Type

Dental

Requirements
Should not have
• Don't use images of teeth

```html
<!DOCTYPE html>
<html lang="en">
<head>
<meta charset="utf-8">
<title>Copperleaf Dental – 2 Years Anniversary Promotion</title>
<link rel="stylesheet" href="https://fonts.googleapis.com/css2?family=Montserrat:wght@400;500;600;700&family=Playfair+Display:wght@400;700&family=Parisienne&family=Lato:wght@400&display=swap">
<style>
  :root {
    --page-bg: #f3f3f3;
    --navy: #13406f;
    --brand-blue: #1d5f9c;
    --mid-blue: #2f78b4;
    --sky-blue: #9cc6e6;
    --pale-blue: #d6e8f5;
    --accent-blue: #3b8fd0;
    --ink: #1c2b3a;
    --white: #ffffff;
  }
  * { box-sizing: border-box; margin: 0; padding: 0; }
  html, body { width: 1200px; height: 1200px; overflow: hidden; }
  body { background: var(--page-bg); position: relative; font-family: "Montserrat", sans-serif; }

  .flyer {
    position: absolute; left: 248px; top: 103px;
    width: 704px; height: 994px; overflow: hidden;
    background: linear-gradient(180deg, var(--white) 0%, #eef5fb 20%, var(--pale-blue) 34%, var(--sky-blue) 55%, var(--mid-blue) 82%, var(--brand-blue) 100%);
  }
  .flyer__facets { position: absolute; inset: 0; }

  .brand {
    position: absolute; left: 30px; top: 110px; width: 240px;
    text-align: center; color: var(--navy);
    font-family: "Montserrat", sans-serif; font-weight: 600;
  }
  .brand__mark { width: 46px; height: 46px; background: var(--brand-blue); margin: 0 auto 16px; }
  .brand__name { font-size: 24px; letter-spacing: 2px; line-height: 1.3; }

  .promo {
    position: absolute; left: 312px; top: 22px; width: 392px;
    text-align: center; color: var(--white);
  }
  .promo__kicker { font-size: 37px; font-weight: 500; letter-spacing: 1.5px; line-height: 1.1; }
  .promo__title { font-size: 49px; font-weight: 700; letter-spacing: 1px; line-height: 1.05; }
  .promo__rule { width: 300px; margin: 8px auto 8px; border-top: 2px dotted var(--white); }
  .promo__dates { font-size: 19px; font-weight: 500; }
  .promo__until {
    display: inline-block; margin-top: 6px; padding: 2px 20px;
    background: var(--navy); border: 1.5px solid var(--white); border-radius: 20px;
    font-size: 19px; font-weight: 500;
  }

  .milestone { position: absolute; left: 210px; top: 215px; width: 420px; height: 200px; }
  .milestone__number {
    position: absolute; left: 0; top: -30px;
    font-family: "Playfair Display", serif; font-weight: 400;
    font-size: 210px; line-height: 1; color: var(--brand-blue);
  }
  .milestone__years {
    position: absolute; left: 112px; top: 40px;
    font-family: "Parisienne", cursive; font-size: 56px; color: var(--accent-blue);
  }
  .milestone__label {
    position: absolute; left: 96px; top: 116px;
    font-family: "Playfair Display", serif; font-weight: 700;
    font-size: 27px; letter-spacing: 0.5px; color: var(--ink);
  }

  .promo-copy {
    position: absolute; left: 239px; top: 466px; width: 436px;
    font-family: "Lato", sans-serif; font-size: 15px; line-height: 20px;
    text-align: justify; color: var(--ink);
  }

  .family-photo {
    position: absolute; left: 294px; top: 608px; width: 398px; height: 321px;
    background: radial-gradient(ellipse at 50% 45%, #e9d2c2 0%, #c9a48e 35%, #6f8fb0 75%, var(--mid-blue) 100%);
    opacity: 0.9;
  }

  .tagline {
    position: absolute; left: 22px; top: 770px;
    color: var(--white); font-size: 39px; line-height: 45px; font-weight: 400;
  }
  .tagline strong { font-weight: 600; display: block; }

  .footer {
    position: absolute; left: 0; bottom: 0; width: 704px; height: 65px;
    background: var(--white); display: flex; align-items: center;
  }
  .footer__phone-band { position: absolute; left: 0; top: 0; width: 290px; height: 65px; }
  .footer__phone {
    position: absolute; left: 86px; top: 0; line-height: 65px;
    color: var(--white); font-size: 25px; font-weight: 700; letter-spacing: 0.5px;
  }
  .footer__contact {
    position: absolute; right: 38px; top: 0; line-height: 65px;
    color: var(--ink); font-size: 18px; font-weight: 600;
  }
  .footer__divider { color: var(--accent-blue); margin: 0 10px; }
</style>
</head>
<body>
  <main class="flyer">
    <svg class="flyer__facets" width="704" height="994" viewBox="0 0 704 994" aria-hidden="true">
      <polygon points="0,330 250,300 120,560 0,620" fill="#ffffff" opacity="0.25"/>
      <polygon points="0,620 120,560 90,760 0,800" fill="#ffffff" opacity="0.12"/>
      <polygon points="312,0 704,0 704,300 470,240 312,250" fill="#1d5f9c"/>
      <polygon points="312,250 470,240 560,420 704,300 704,340 590,450" fill="#2a70ae"/>
      <polygon points="470,240 704,300 560,420" fill="#1a5590"/>
      <polygon points="312,0 420,0 312,140" fill="#245f98"/>
    </svg>

    <div class="brand">
      <div class="brand__mark"></div>
      <div class="brand__name">COPPERLEAF<br>DENTAL</div>
    </div>

    <header class="promo">
      <div class="promo__kicker">ANNIVERSARY</div>
      <h1 class="promo__title">PROMOTION</h1>
      <div class="promo__rule"></div>
      <p class="promo__dates">Promotion runs from Now</p>
      <p class="promo__until">until 31st Dec 2024</p>
    </header>

    <section class="milestone">
      <span class="milestone__number">2</span>
      <span class="milestone__years">Years</span>
      <span class="milestone__label">ANNIVERSARY</span>
    </section>

    <p class="promo-copy">Lorem ipsum dolor sit amet, consectetur adipiscing elit. Sed volutpat pretium pharetra. Maecenas porta diam justo, vitae hendrerit nisi commodo et. Quisque eu metus condimentum, suscipit augue nec, hendrerit enim. Fusce vitae fringilla nisi, ultrices congue urna. In porttitor lacinia mi at accumsan. Donec pharetra mi a sem cursus congue.</p>

    <div class="family-photo" role="img" aria-label="Photo of a smiling family: a father, mother and young daughter in white shirts"></div>

    <p class="tagline">Make<br>Your Smile<strong>Brighter</strong></p>

    <footer class="footer">
      <svg class="footer__phone-band" width="290" height="65" viewBox="0 0 290 65" aria-hidden="true">
        <polygon points="0,0 270,0 290,65 0,65" fill="#13406f"/>
        <polygon points="0,0 50,0 62,65 0,65" fill="#2f78b4"/>
        <path d="M18 22c2-2 4-2 5 0l3 4c1 2 0 3-1 4l-1 1c1 3 4 6 7 7l1-1c1-1 2-2 4-1l4 3c2 1 2 3 0 5l-2 2c-2 2-6 1-11-3s-9-10-10-13c-1-3 0-5 1-6z" fill="#ffffff"/>
      </svg>
      <span class="footer__phone">555 013 2024</span>
      <span class="footer__contact">Address , City, Zip Code<span class="footer__divider">|</span>Website</span>
    </footer>
  </main>
</body>
</html>
```